Investment company needing business card

We are wanting a business card which looks sharp and easy on the eye. We are thinking of having a business card with the logo embossed on it, to really make it stand out. We will only have a small amount of information of the business card, person's name, position, email address and phone number

Contact Information for Business Card

Danielle Frost
Executive Assistant
+64 21 473 5162
danielf@harwickpartners.co.nz

Requirements
Must have
• Embossed logo
Should not have
• Not to be busy

```html
<!DOCTYPE html>
<html lang="en">
<head>
<meta charset="utf-8">
<title>Harwick Partners – Business Card</title>
<link href="https://fonts.googleapis.com/css2?family=Source+Sans+3:wght@400;600;700&display=swap" rel="stylesheet">
<style>
  :root {
    --backdrop: #e0e0e0;
    --card: #f4f4f4;
    --green: #23b574;
    --grey: #636466;
    --text-grey: #555657;
    --white: #ffffff;
  }
  * { margin: 0; padding: 0; box-sizing: border-box; }
  html, body {
    width: 1130px; height: 1200px; overflow: hidden;
    background: var(--backdrop);
    font-family: "Source Sans 3", "Myriad Pro", Arial, sans-serif;
  }
  .canvas { position: relative; width: 1130px; height: 1200px; }
  .card {
    position: absolute;
    background: var(--card);
    border-radius: 16px;
    overflow: hidden;
    box-shadow: 0 3px 10px rgba(0,0,0,0.18);
  }
  .card--front { left: 383px; top: 74px; width: 364px; height: 636px; }
  .card--back { left: 246px; top: 748px; width: 637px; height: 364px; }

  .brand {
    position: absolute; left: 0; right: 0;
    display: flex; align-items: center; justify-content: center; gap: 10px;
    color: var(--green); font-weight: 700; letter-spacing: 1px;
    text-transform: uppercase;
  }
  .brand__square { background: var(--grey); }
  .card--front .brand { top: 110px; font-size: 26px; }
  .card--front .brand__square { width: 22px; height: 22px; }
  .card--back .brand { top: 160px; font-size: 38px; }
  .card--back .brand__square { width: 34px; height: 34px; }

  .person { position: absolute; top: 301px; left: 0; right: 0; text-align: center; }
  .person__name { color: var(--green); font-weight: 700; font-size: 22px; letter-spacing: 0.3px; line-height: 1.1; }
  .person__role { color: var(--text-grey); font-size: 16px; margin-top: 4px; }

  .contact { position: absolute; left: 13px; top: 384px; width: 337px; }
  .contact__row { display: flex; height: 27px; margin-bottom: 3px; }
  .contact__label {
    width: 79px; background: var(--grey); color: var(--white);
    border-radius: 5px 0 0 0; font-size: 16px;
    display: flex; align-items: center; justify-content: center;
  }
  .contact__value {
    flex: 1; margin-left: 3px; background: var(--green); color: var(--white);
    border-radius: 0 4px 4px 0; font-size: 16px;
    display: flex; align-items: center; padding-left: 6px; white-space: nowrap;
  }
  .wave { position: absolute; left: 0; bottom: 0; width: 364px; height: 110px; display: block; }
</style>
</head>
<body>
<div class="canvas">
  <section class="card card--front">
    <div class="brand"><span class="brand__square"></span>Harwick Partners</div>
    <div class="person">
      <p class="person__name">DANIELLE FROST</p>
      <p class="person__role">Executive Assistant</p>
    </div>
    <div class="contact">
      <div class="contact__row"><span class="contact__label">Phone</span><span class="contact__value">+64 21 473 5162</span></div>
      <div class="contact__row"><span class="contact__label">Email</span><span class="contact__value">danielf@harwickpartners.co.nz</span></div>
      <div class="contact__row"><span class="contact__label">Website</span><span class="contact__value">www.harwickpartners.co.nz</span></div>
    </div>
    <svg class="wave" viewBox="0 0 364 110" preserveAspectRatio="none">
      <path d="M0 30 C40 8 100 8 150 30 C200 54 270 80 364 24 L364 50 C270 100 200 84 150 58 C100 32 40 26 0 48 Z" fill="var(--grey)"/>
      <path d="M0 47 C40 22 100 22 150 46 C200 70 270 100 364 56 V110 H0 Z" fill="var(--green)" stroke="var(--white)" stroke-width="2.5"/>
    </svg>
  </section>

  <section class="card card--back">
    <div class="brand"><span class="brand__square"></span>Harwick Partners</div>
  </section>
</div>
</body>
</html>
```